Road Construction Company needs business cards

We would like a new business card designed for our business.

We're a road construction company based in Qld, Australia.

Can the business card please have the following information on it.

Name: Warren Halbeck
Position: General Manager
Phone: 0472 915 348
Email: Warren.halbeck@tovrin.com.au
Address: 87 Marrow Ave, Pendlebay, QLD, 4023
Website: www.tovrin.com.au

Visually we'd like the card to be professional and simple.

Attached is our logo.

Our website is www.tovrin.com.au

Target Market(s)

Men aged 25-60

Contact Information for Business Card

As listed in project description

Font styles to use
Serif

Requirements
Must have
• Large logo on back of card

```html
<!DOCTYPE html>
<html lang="en">
<head>
<meta charset="utf-8">
<title>Tovrin Business Card</title>
<link href="https://fonts.googleapis.com/css2?family=Oxanium:wght@400;500;700&display=swap" rel="stylesheet">
<style>
  :root {
    --backdrop: #979797;
    --card-dark: #232323;
    --card-light: #ffffff;
    --brand-navy: #0b4f9d;
    --brand-sky: #2a9fd6;
    --ink: #1f1f1f;
    --rule: #9a9a9a;
    --tint: #f2f2f2;
  }
  * { margin: 0; padding: 0; box-sizing: border-box; }
  html, body { width: 1200px; height: 1000px; overflow: hidden; }
  body {
    background: var(--backdrop);
    font-family: "Oxanium", sans-serif;
    position: relative;
  }
  .card {
    position: absolute;
    left: 293px;
    width: 615px;
    height: 350px;
    border-radius: 28px;
    overflow: hidden;
  }
  .card-back { top: 121px; background: var(--card-dark); }
  .card-front { top: 533px; background: var(--card-light); }

  .back-pattern {
    position: absolute; inset: 0;
    background: linear-gradient(90deg, #1b1b1b 0%, #262626 55%, #343434 100%);
  }
  .back-wordmark {
    position: absolute;
    left: 626px; left: 333px;
    top: 236px;
    font-size: 38px;
    font-weight: 700;
    letter-spacing: 2px;
    color: #ffffff;
    line-height: 1;
  }

  .front-accent { position: absolute; inset: 0; }
  .front-wordmark {
    position: absolute;
    left: 28px; top: 44px;
    font-size: 36px;
    font-weight: 700;
    letter-spacing: 2px;
    color: var(--brand-navy);
    line-height: 1;
  }
  .person-name {
    position: absolute; left: 28px; top: 138px;
    font-size: 19px; font-weight: 700; letter-spacing: 1px;
    color: var(--brand-navy); text-transform: uppercase;
  }
  .person-role {
    position: absolute; left: 28px; top: 158px;
    font-size: 16px; font-weight: 400; color: var(--brand-sky);
  }
  .divider {
    position: absolute; left: 28px; top: 187px;
    width: 564px; height: 1px; background: var(--rule);
  }
  .address {
    position: absolute; left: 28px; top: 200px;
    font-size: 16px; line-height: 19px; color: var(--ink); font-style: normal;
  }
  .contact-list {
    position: absolute; left: 28px; top: 257px;
    list-style: none; font-size: 16px; color: var(--ink);
  }
  .contact-list li {
    display: flex; align-items: center; height: 20px;
  }
  .contact-list svg { width: 16px; height: 16px; margin-right: 12px; flex: none; }
</style>
</head>
<body>

<section class="card card-back">
  <div class="back-pattern" role="img" aria-label="Repeating embossed pattern of the brand symbol"></div>
  <div class="back-wordmark">TOVRIN</div>
</section>

<section class="card card-front">
  <svg class="front-accent" viewBox="0 0 615 350" role="img" aria-label="Large faint brand symbol decoration">
    <polygon points="467,0 615,0 615,350 285,350" fill="var(--tint)"/>
  </svg>

  <div class="front-wordmark">TOVRIN</div>

  <h1 class="person-name">Warren Halbeck</h1>
  <p class="person-role">General Manager</p>
  <div class="divider"></div>

  <address class="address">87 Marrow Ave,<br>Pendlebay, QLD, 4023</address>

  <ul class="contact-list">
    <li>
      <svg viewBox="0 0 16 16"><path d="M3 1.5l2.5 0 1.2 3-1.6 1.2c.8 1.8 2.2 3.2 4 4l1.2-1.6 3 1.2 0 2.5c0 .8-.7 1.4-1.5 1.3C6.5 12.5 3.5 9.5 2.9 3c-.1-.8.5-1.5 1.3-1.5z" fill="var(--brand-sky)"/></svg>
      0472 915 348
    </li>
    <li>
      <svg viewBox="0 0 16 16"><rect x="1" y="3" width="14" height="10" fill="var(--brand-sky)"/><path d="M1.5 3.5 8 9l6.5-5.5M1.5 12.5l5-4.5M14.5 12.5l-5-4.5" stroke="#fff" stroke-width="1" fill="none"/></svg>
      Warren.halbeck@tovrin.com.au
    </li>
    <li>
      <svg viewBox="0 0 16 16"><circle cx="8" cy="8" r="6.5" fill="var(--brand-sky)"/><g stroke="#fff" stroke-width=".8" fill="none"><ellipse cx="8" cy="8" rx="2.8" ry="6.5"/><path d="M1.5 8h13M2.5 5h11M2.5 11h11M8 1.5v13"/></g></svg>
      www.tovrin.com.au
    </li>
  </ul>
</section>

</body>
</html>
```